Car transport business

We need a new business card design. Attached is our old card sample. I would just like to adjust the logo colors (blue and red) to be brighter. I changed my name to the brighter red and the word dispatcher to a brighter blue as an example. But you can adjust those colors further. And then perhaps you can use the same colors for the card design but use your imagination.

As a suggestion so the card stands out I would like to add a clip art of car carrier truck. Attached are examples of that as well

```html
<!DOCTYPE html>
<html lang="en">
<head>
<meta charset="UTF-8">
<title>Northline Haul – Business Card</title>
<link rel="stylesheet" href="https://fonts.googleapis.com/css2?family=Roboto:wght@400;500&family=Russo+One&display=swap">
<style>
  :root {
    --stage: #262626;
    --paper: #ffffff;
    --brand-blue: #1e6fc4;
    --brand-red: #e8202a;
    --rule: #c8c8c8;
    --truck-grey: #b4b4b4;
  }
  * { box-sizing: border-box; margin: 0; padding: 0; }
  html, body { width: 1200px; height: 900px; overflow: hidden; }
  body {
    background: var(--stage);
    font-family: "Roboto", Arial, sans-serif;
    position: relative;
  }
  .card {
    position: absolute;
    width: 600px;
    height: 343px;
    background: var(--paper);
    overflow: hidden;
  }
  .card--contact { left: 130px; top: 70px; border-bottom: 5px solid var(--brand-blue); }
  .card--brand { left: 470px; top: 480px; border-bottom: 5px solid var(--brand-red); }

  /* contact side */
  .identity {
    position: absolute;
    left: 120px;
    top: 136px;
    text-align: right;
    width: 180px;
  }
  .identity__name {
    font-size: 30px;
    font-weight: 500;
    letter-spacing: 0.5px;
    line-height: 1;
  }
  .identity__first { color: var(--brand-blue); }
  .identity__last { color: var(--brand-red); }
  .identity__role {
    color: var(--brand-blue);
    font-size: 14px;
    letter-spacing: 1px;
    margin-top: 4px;
  }
  .divider {
    position: absolute;
    left: 322px;
    top: 128px;
    width: 1px;
    height: 76px;
    background: var(--rule);
  }
  .contacts {
    position: absolute;
    left: 340px;
    top: 132px;
    list-style: none;
  }
  .contacts li {
    display: flex;
    align-items: center;
    gap: 8px;
    color: var(--brand-red);
    font-size: 15px;
    line-height: 22px;
  }
  .contacts svg { width: 14px; height: 14px; fill: var(--brand-blue); flex: none; }

  /* brand side */
  .brand {
    position: absolute;
    left: 70px;
    top: 58px;
    display: flex;
    align-items: center;
    gap: 14px;
  }
  .brand__dot {
    width: 44px;
    height: 44px;
    border-radius: 50%;
    background: var(--brand-blue);
  }
  .brand__name {
    font-family: "Russo One", Arial, sans-serif;
    font-size: 40px;
    color: var(--brand-red);
    letter-spacing: 1px;
    line-height: 1;
  }
  .brand__tagline {
    position: absolute;
    left: 130px;
    top: 108px;
    font-size: 12px;
    letter-spacing: 3px;
    color: var(--brand-blue);
    text-transform: uppercase;
  }
  .truck-art {
    position: absolute;
    left: 60px;
    right: 40px;
    top: 140px;
    bottom: 22px;
    background: linear-gradient(180deg, #c4c4c4 0%, var(--truck-grey) 100%);
    border-radius: 18px 60px 10px 10px;
  }
</style>
</head>
<body>

<section class="card card--contact" aria-label="Business card, contact side">
  <div class="identity">
    <p class="identity__name"><span class="identity__first">LEON</span> <span class="identity__last">VARGA</span></p>
    <p class="identity__role">DIAPATCHER</p>
  </div>
  <div class="divider"></div>
  <ul class="contacts">
    <li>
      <svg viewBox="0 0 24 24" aria-hidden="true"><path d="M6.6 10.8a15 15 0 0 0 6.6 6.6l2.2-2.2a1 1 0 0 1 1-.25 11.4 11.4 0 0 0 3.6.57 1 1 0 0 1 1 1V20a1 1 0 0 1-1 1A17 17 0 0 1 3 4a1 1 0 0 1 1-1h3.5a1 1 0 0 1 1 1c0 1.25.2 2.45.57 3.57a1 1 0 0 1-.25 1z"/></svg>
      312-555-0148
    </li>
    <li>
      <svg viewBox="0 0 24 24" aria-hidden="true"><path d="M6 2h12v6H6zM3 9h18a1 1 0 0 1 1 1v7h-4v5H6v-5H2v-7a1 1 0 0 1 1-1zm5 8v3h8v-3z"/></svg>
      312-555-0179
    </li>
    <li>
      <svg viewBox="0 0 24 24" aria-hidden="true"><path d="M2 5h20v14H2zm2 2v.5l8 5 8-5V7l-8 5z"/></svg>
      northlinehaul@mail.com
    </li>
  </ul>
</section>

<section class="card card--brand" aria-label="Business card, brand side">
  <div class="brand">
    <span class="brand__dot"></span>
    <span class="brand__name">NORTHLINE HAUL</span>
  </div>
  <p class="brand__tagline">The Auto Transport Professionals</p>
  <div class="truck-art" role="img" aria-label="Grey illustration of a car carrier truck loaded with six cars"></div>
</section>

</body>
</html>
```